Business Card Design for Marketing Firm

Looking for business card design for higher end marketing firm. Clean but impressionable/trendy. We are a marketing firm that represents manufacturers in the foodservice equipment and supply industry. Our customers are end users such has hotels, restaurants, country clubs, convention centers and casinos as well as distributors of restaurants supplies and equipment, and manufacturers of foodservice equipment and supplies.
Target Market(s)
Hotels, Restaurants, Supply & Equipment Distributors, Foodservice Manufacturers
Industry/Entity Type
Foodservice/Hospitality
Contact Information for Business Card
Name, Title, Contact Number, Email, Website, Social Media, Address
Requirements
Must have
- Clean & Simple but Serious and Impressionable

```html
<!DOCTYPE html>
<html lang="en">
<head>
<meta charset="utf-8">
<title>Beacon Hospitality Reps – Business Card</title>
<link href="https://fonts.googleapis.com/css2?family=Tinos:wght@400;700&family=Arimo:wght@400&display=swap" rel="stylesheet">
<style>
  :root {
    --navy: #050a7c;
    --navy-light: #2a35b8;
    --paper: #f7f7f8;
    --stripe: #b9bcc2;
    --backdrop: #c9cacd;
    --ink-white: #ffffff;
  }
  * { margin: 0; padding: 0; box-sizing: border-box; }
  html, body { width: 1200px; height: 800px; overflow: hidden; }
  body {
    background: var(--backdrop);
    display: flex; align-items: center; justify-content: center; gap: 60px;
  }
  .card {
    position: relative;
    width: 525px; height: 300px;
    border-radius: 18px;
    overflow: hidden;
    box-shadow: 0 6px 18px rgba(0,0,0,.18);
  }
  .card--front { background: var(--paper); }
  .card--back { background: var(--navy); display: flex; align-items: center; justify-content: center; }

  .front-shape { position: absolute; inset: 0; width: 100%; height: 100%; }

  .brand {
    position: absolute; left: 34px; top: 118px;
    color: var(--navy);
    font-family: "Tinos", serif; font-weight: 400;
  }
  .brand__name { font-size: 21px; letter-spacing: 1.5px; text-transform: uppercase; white-space: nowrap; }
  .brand__rule { height: 1px; background: var(--navy); margin: 4px 0 3px; width: 240px; }
  .brand__sub { font-size: 12px; letter-spacing: 2px; text-align: right; width: 240px; }

  .contact {
    position: absolute; right: 26px; top: 26px;
    color: var(--ink-white); text-align: right;
    font-family: "Arimo", sans-serif;
  }
  .contact__list { list-style: none; font-size: 11.5px; line-height: 1.45; }
  .contact__list li { display: flex; justify-content: flex-end; align-items: center; gap: 7px; }
  .contact__list svg { width: 10px; height: 10px; fill: var(--ink-white); }
  .contact__address { font-style: normal; font-size: 11.5px; line-height: 1.4; margin-top: 14px; }
  .person { margin-top: 22px; }
  .person__name { font-family: "Tinos", serif; font-weight: 700; font-size: 20px; letter-spacing: 1px; text-transform: uppercase; }
  .person__title { font-size: 11.5px; }

  .back-brand {
    font-family: "Tinos", serif; font-weight: 400;
    font-size: 40px; letter-spacing: 6px;
    color: var(--navy-light); text-transform: uppercase;
  }
</style>
</head>
<body>
  <section class="card card--front" aria-label="Business card front">
    <svg class="front-shape" viewBox="0 0 525 300" preserveAspectRatio="none" aria-hidden="true">
      <line x1="292" y1="0" x2="244" y2="300" stroke="var(--stripe)" stroke-width="3"/>
      <line x1="300" y1="0" x2="252" y2="300" stroke="var(--stripe)" stroke-width="2"/>
      <polygon points="306,0 525,0 525,300 258,300" fill="var(--navy)"/>
    </svg>

    <div class="brand">
      <div class="brand__name">Beacon Hospitality</div>
      <div class="brand__rule"></div>
      <div class="brand__sub">REPS</div>
    </div>

    <div class="contact">
      <ul class="contact__list">
        <li>(555) 0142-7781
          <svg viewBox="0 0 10 10"><path d="M2 0.5h2l.8 2.4-1.2.9a6 6 0 0 0 2.6 2.6l.9-1.2L9.5 6v2A1.5 1.5 0 0 1 8 9.5 7.5 7.5 0 0 1 .5 2 1.5 1.5 0 0 1 2 .5z"/></svg>
        </li>
        <li>name@BEACONREPS.com
          <svg viewBox="0 0 10 10"><path d="M0 2h10v6H0z M0.6 2.4 5 5.6l4.4-3.2" stroke="var(--navy)" stroke-width=".8"/></svg>
        </li>
        <li>www.BEACONREPS.com
          <svg viewBox="0 0 10 10"><circle cx="5" cy="5" r="4.6"/><path d="M.5 5h9M5 .5c-2 2.5-2 6.5 0 9M5 .5c2 2.5 2 6.5 0 9" stroke="var(--navy)" stroke-width=".7" fill="none"/></svg>
        </li>
      </ul>
      <address class="contact__address">27 Harbor Lane<br>Millbrook, NY 10000</address>
      <div class="person">
        <div class="person__name">Evan Carter</div>
        <div class="person__title">President</div>
      </div>
    </div>
  </section>

  <section class="card card--back" aria-label="Business card back">
    <div class="back-brand">Beacon</div>
  </section>
</body>
</html>
```